Wordpress Website design partner needed for an Arabic Language Institute for English Speakers

We are an online Arabic Language institute, targeting English Speakers around the world and we provide online courses and private group and one on one classes
We are looking for a total of 5 pages designed.
The Design should be mobile-first, and then provide PC for any differences.
I am looking for a consistent design with a lot of white space and in line with our Logo colours.
Images used should be around the theme of Arabic Language/Islamic in Nature, so please do not use any illustrations or images of animals or human beings except for silhouettes or images without faces visible, such as someone facing other way or below torso or hands etc.
The website will eventually be prepared for Wordpress using Divi.
I will provide a very structured outline of what elements and modules each page should have. Therefore I am looking for someone that has an eye for detail and is precise in executing requirements.
I decided to post on this site because I am looking for a long-term partner that can take care of any of our design needs as they come up.
More details to follow
I will do abit more research tomorrow to suggest sample sites
Updates
Target Market(s)
English speakers that want to learn Arabic for Religous purposes such as understanding the Quran
Industry/Entity Type
Education
Colors
Designer to choose colors to be used in the design.
Requirements
Must have
- Mobile First, and design for PC for changes
- Consistency
- Plenty of White Space
- Colour Palette based on Logo
- Colour and Transparent/White Header for when scrolling
- Big Call to Action buttons with contrasting colors
- A consistent footer for all pages with
- -Social Media Icons
- -Contact us
- -Sitemap
- -Copyright
- -Logo
- Anything with a hashtag (#) beforehand in the Doc file means it should be a module like the modules used in Divi Theme, Please check the following website for an explanation of what each module consists of and some examples of it in use. https://www.pelmorashowcase.net/pelmora-blocks-guide/
Nice to have
- Parallax Effect
Should not have
- illustrations or images of animals or human beings except for silhouettes or images without faces visible, such as someone facing other way or below torso or hands etc.

```html
<!DOCTYPE html>
<html lang="en">
<head>
<meta charset="utf-8">
<title>Courses – Nurqalam Academy</title>
<link rel="stylesheet" href="https://fonts.googleapis.com/css2?family=IBM+Plex+Sans:wght@400;500;600;700&family=Open+Sans:wght@400;600&display=swap">
<style>
:root{
  --hero-blue:#114a98;
  --hero-deep:#0d3f86;
  --teal:#2696aa;
  --ink:#111111;
  --body:#333333;
  --card:#f4f0f0;
  --dark-head:#3a3a3a;
  --footer:#232323;
  --white:#ffffff;
  --line:#cfcfcf;
}
*{margin:0;padding:0;box-sizing:border-box}
html,body{width:1200px;height:2425px;overflow:hidden}
body{position:relative;background:var(--white);font-family:"Open Sans",Arial,sans-serif;color:var(--body)}
.abs{position:absolute}
.heading-font{font-family:"IBM Plex Sans",Arial,sans-serif}

/* hero */
.hero{position:absolute;left:0;top:0;width:1200px;height:368px;background:var(--hero-blue);overflow:hidden}
.hero-skyline{position:absolute;left:0;top:110px;width:1200px;height:258px;background:linear-gradient(90deg,rgba(10,60,130,.9) 0%,rgba(20,80,160,.55) 30%,rgba(17,74,152,0) 55%)}
.nav-link{position:absolute;top:74px;font-family:"IBM Plex Sans",Arial,sans-serif;font-weight:500;font-size:16px;color:var(--white);letter-spacing:.3px;text-decoration:none}
.nav-link.active{color:var(--teal);text-decoration:underline}
.nav-divider{position:absolute;top:66px;width:1px;height:33px;background:rgba(255,255,255,.8)}
.brand-top{position:absolute;left:530px;top:70px;width:140px;text-align:center;font-family:"IBM Plex Sans",Arial,sans-serif;font-weight:600;font-size:17px;color:var(--white);letter-spacing:1px}
.login-btn{position:absolute;left:972px;top:65px;width:93px;height:39px;border:2px solid var(--white);border-radius:20px;color:var(--white);font-family:"IBM Plex Sans",Arial,sans-serif;font-weight:600;font-size:14px;line-height:35px;text-align:center}
.hero-title{position:absolute;left:0;top:226px;width:1200px;text-align:center;font-family:"IBM Plex Sans",Arial,sans-serif;font-weight:600;font-size:38px;color:var(--white);letter-spacing:.5px}

/* section headings */
.section-title{position:absolute;left:0;width:1200px;text-align:center;font-family:"IBM Plex Sans",Arial,sans-serif;font-weight:600;font-size:26px;color:var(--ink)}
.section-rule{position:absolute;left:574px;width:52px;height:3px;background:var(--teal)}

/* course cards */
.course-card{position:absolute;width:298px;height:369px;background:var(--card)}
.course-photo{width:298px;height:200px}
.course-title{position:absolute;left:25px;top:222px;font-family:"IBM Plex Sans",Arial,sans-serif;font-weight:600;font-size:16px;color:var(--ink)}
.course-text{position:absolute;left:25px;top:249px;width:260px;font-size:12.5px;line-height:16px;color:var(--body)}
.read-more{position:absolute;left:25px;top:317px;width:83px;height:28px;border-radius:14px;background:var(--teal);color:var(--white);font-family:"IBM Plex Sans",Arial,sans-serif;font-weight:600;font-size:9.5px;line-height:28px;text-align:center}

/* pricing */
.pricing{position:absolute;left:0;top:1343px;width:1200px;height:678px;background:var(--card)}
.plan{position:absolute;background:var(--white);border:1px solid var(--line)}
.plan-head{position:absolute;left:0;top:0;width:100%;background:var(--dark-head);color:var(--white);font-family:"IBM Plex Sans",Arial,sans-serif;font-weight:500;font-size:17px;text-align:center}
.plan.featured .plan-head{background:var(--teal)}
.plan-price{position:absolute;left:0;width:100%;text-align:center;font-family:"IBM Plex Sans",Arial,sans-serif;font-weight:600;font-size:56px;color:var(--teal);line-height:1}
.plan-price sup{font-size:28px;vertical-align:top;position:relative;top:2px}
.plan-split{position:absolute;left:0;width:100%;height:1px;background:var(--line)}
.plan-list{position:absolute;left:32px;list-style:none}
.plan-list li{position:relative;height:30.5px;padding-left:18px;font-size:13.5px;color:var(--body)}
.plan-list li::before{content:"";position:absolute;left:0;top:6px;border-left:5px solid var(--ink);border-top:4px solid transparent;border-bottom:4px solid transparent}
.signup-btn{position:absolute;width:87px;height:35px;border-radius:18px;background:var(--teal);color:var(--white);font-family:"IBM Plex Sans",Arial,sans-serif;font-weight:500;font-size:12.5px;line-height:35px;text-align:center}

/* footer */
.footer{position:absolute;left:0;top:2021px;width:1200px;height:404px;background:var(--footer);color:var(--white)}
.footer-label{position:absolute;font-family:"IBM Plex Sans",Arial,sans-serif;font-weight:500;font-size:14.5px;letter-spacing:.3px}
.icon-dot{position:absolute;width:34px;height:34px;border-radius:50%;background:var(--teal)}
.icon-dot svg{position:absolute;left:9px;top:9px}
.contact-small{position:absolute;font-family:"IBM Plex Sans",Arial,sans-serif;font-weight:500;font-size:12.5px;line-height:17px}
.contact-small b{display:block;font-weight:600;font-size:14.5px}
.social-text{position:absolute;font-family:"IBM Plex Sans",Arial,sans-serif;font-size:14px;line-height:19px;color:#e8e8e8}
.brand-frame{position:absolute;left:429px;top:59px;width:342px;height:168px;border:1px solid #bdbdbd;border-top:none}
.brand-frame-gap{position:absolute;left:525px;top:222px;width:150px;height:10px;background:var(--footer)}
.brand-foot{position:absolute;left:429px;top:150px;width:342px;text-align:center;font-family:"IBM Plex Sans",Arial,sans-serif;font-weight:600;font-size:20px;letter-spacing:2px;color:var(--white)}
.footer-nav{position:absolute;left:0;top:257px;width:1200px;text-align:center;font-family:"IBM Plex Sans",Arial,sans-serif;font-weight:500;font-size:14px}
.footer-nav span{margin:0 7px}
.footer-rule{position:absolute;left:130px;top:319px;width:938px;height:1px;background:#4a4a4a}
.copyright{position:absolute;left:0;top:355px;width:1182px;text-align:center;font-size:11.5px;color:#dddddd}
</style>
</head>
<body>

<header class="hero">
  <div class="hero-skyline" role="img" aria-label="Faint blue silhouette of a domed mosque and minaret"></div>
  <a class="nav-link" style="left:314px">HOME</a>
  <div class="nav-divider" style="left:392px"></div>
  <a class="nav-link" style="left:421px">ABOUT US</a>
  <div class="brand-top">NURQALAM</div>
  <a class="nav-link active" style="left:691px">COURSES</a>
  <div class="nav-divider" style="left:787px"></div>
  <a class="nav-link" style="left:815px">CONTACT US</a>
  <div class="login-btn">LOGIN</div>
  <h1 class="hero-title">COURSES</h1>
</header>

<h2 class="section-title" style="top:412px">OUR COURSES</h2>
<div class="section-rule" style="top:460px"></div>

<article class="course-card" style="left:130px;top:506px">
  <div class="course-photo" role="img" aria-label="White marble mosque with domes and minarets reflected in water" style="background:linear-gradient(180deg,#7fb2dc 0%,#d9e3ee 55%,#c8b7a8 80%,#8fb2c9 100%)"></div>
  <h3 class="course-title">LOREM IPSUM IS SIMPLY</h3>
  <p class="course-text">Lorem ipsum dolor sit amet, consectetur adipiscing elit, sed do eiusod tempor incididunt ut labore et dolore.</p>
  <div class="read-more">READ MORE</div>
</article>
<article class="course-card" style="left:451px;top:506px">
  <div class="course-photo" role="img" aria-label="Golden dome shrine among trees under a dramatic blue sky" style="background:linear-gradient(180deg,#2f6fbf 0%,#8db3d8 40%,#4f5a3a 70%,#2e3d22 100%)"></div>
  <h3 class="course-title">LOREM IPSUM IS SIMPLY</h3>
  <p class="course-text">Lorem ipsum dolor sit amet, consectetur adipiscing elit, sed do eiusod tempor incididunt ut labore et dolore.</p>
  <div class="read-more">READ MORE</div>
</article>
<article class="course-card" style="left:770px;top:506px">
  <div class="course-photo" role="img" aria-label="Silhouette of a person praying inside a sunlit arched doorway" style="background:radial-gradient(ellipse at 50% 45%,#d9c08a 0%,#7a5a32 35%,#2e2118 75%)"></div>
  <h3 class="course-title">LOREM IPSUM IS SIMPLY</h3>
  <p class="course-text">Lorem ipsum dolor sit amet, consectetur adipiscing elit, sed do eiusod tempor incididunt ut labore et dolore.</p>
  <div class="read-more">READ MORE</div>
</article>

<article class="course-card" style="left:130px;top:898px">
  <div class="course-photo" role="img" aria-label="Silhouette of a veiled woman on a beach at sunset" style="background:linear-gradient(180deg,#e9b196 0%,#f0a272 45%,#6b6f7c 70%,#3c4352 100%)"></div>
  <h3 class="course-title">LOREM IPSUM IS SIMPLY</h3>
  <p class="course-text">Lorem ipsum dolor sit amet, consectetur adipiscing elit, sed do eiusod tempor incididunt ut labore et dolore.</p>
  <div class="read-more">READ MORE</div>
</article>
<article class="course-card" style="left:451px;top:898px">
  <div class="course-photo" role="img" aria-label="Dark silhouette of raised hands in prayer against a setting sun" style="background:radial-gradient(ellipse at 65% 45%,#d8d7b0 0%,#4f6b5e 30%,#0f2420 70%)"></div>
  <h3 class="course-title">LOREM IPSUM IS SIMPLY</h3>
  <p class="course-text">Lorem ipsum dolor sit amet, consectetur adipiscing elit, sed do eiusod tempor incididunt ut labore et dolore.</p>
  <div class="read-more">READ MORE</div>
</article>
<article class="course-card" style="left:770px;top:898px">
  <div class="course-photo" role="img" aria-label="Hands holding prayer beads over a red patterned prayer rug" style="background:linear-gradient(135deg,#c9694f 0%,#b9474a 40%,#4d6e9c 70%,#8f6e57 100%)"></div>
  <h3 class="course-title">LOREM IPSUM IS SIMPLY</h3>
  <p class="course-text">Lorem ipsum dolor sit amet, consectetur adipiscing elit, sed do eiusod tempor incididunt ut labore et dolore.</p>
  <div class="read-more">READ MORE</div>
</article>

<section class="pricing">
  <h2 class="section-title" style="top:45px">PRICING</h2>
  <div class="section-rule" style="top:93px"></div>

  <div class="plan" style="left:144px;top:170px;width:306px;height:428px">
    <div class="plan-head" style="height:41px;line-height:41px">LOREM IPSUM</div>
    <div class="plan-price" style="top:70px"><sup>$</sup>69</div>
    <div class="plan-split" style="top:136px"></div>
    <ul class="plan-list" style="top:172px">
      <li>Lorem Ipsum is simply dummy</li><li>Contrary to popular belief</li><li>There are many variations</li><li>eiusmod tempor incididunt ut</li><li>On the other hand, we denounce</li><li>Welcomed and every pain</li>
    </ul>
    <div class="signup-btn" style="left:99px;top:367px">SIGN UP</div>
  </div>

  <div class="plan featured" style="left:449px;top:136px;width:305px;height:488px">
    <div class="plan-head" style="height:75px;line-height:73px">LOREM IPSUM</div>
    <div class="plan-price" style="top:104px"><sup>$</sup>89</div>
    <div class="plan-split" style="top:170px"></div>
    <ul class="plan-list" style="top:206px">
      <li>Lorem Ipsum is simply dummy</li><li>Contrary to popular belief</li><li>There are many variations</li><li>eiusmod tempor incididunt ut</li><li>On the other hand, we denounce</li><li>Welcomed and every pain</li>
    </ul>
    <div class="signup-btn" style="left:98px;top:401px">SIGN UP</div>
  </div>

  <div class="plan" style="left:753px;top:170px;width:301px;height:428px">
    <div class="plan-head" style="height:41px;line-height:41px">LOREM IPSUM</div>
    <div class="plan-price" style="top:70px"><sup>$</sup>129</div>
    <div class="plan-split" style="top:136px"></div>
    <ul class="plan-list" style="top:172px">
      <li>Lorem Ipsum is simply dummy</li><li>Contrary to popular belief</li><li>There are many variations</li><li>eiusmod tempor incididunt ut</li><li>On the other hand, we denounce</li><li>Welcomed and every pain</li>
    </ul>
    <div class="signup-btn" style="left:96px;top:367px">SIGN UP</div>
  </div>
</section>

<footer class="footer">
  <div class="footer-label" style="left:136px;top:58px">CONTACT US</div>

  <div class="icon-dot" style="left:132px;top:103px">
    <svg width="16" height="16" viewBox="0 0 24 24"><path fill="#fff" d="M6.6 10.8a15.1 15.1 0 0 0 6.6 6.6l2.2-2.2a1 1 0 0 1 1-.25 11.4 11.4 0 0 0 3.6.57 1 1 0 0 1 1 1V20a1 1 0 0 1-1 1A17 17 0 0 1 3 4a1 1 0 0 1 1-1h3.5a1 1 0 0 1 1 1c0 1.25.2 2.45.57 3.57a1 1 0 0 1-.25 1z"/></svg>
  </div>
  <div class="contact-small" style="left:182px;top:104px">CALL US<b>888.888.8888</b></div>

  <div class="icon-dot" style="left:132px;top:175px">
    <svg width="16" height="16" viewBox="0 0 24 24"><path fill="#fff" d="M3 5h18a1 1 0 0 1 1 1v1l-10 6L2 7V6a1 1 0 0 1 1-1zm-1 4.3 10 6 10-6V18a1 1 0 0 1-1 1H3a1 1 0 0 1-1-1z"/></svg>
  </div>
  <div class="contact-small" style="left:182px;top:176px">E MAIL US<b>info@nurqalam-academy.org</b></div>

  <div class="brand-frame"></div>
  <div class="brand-frame-gap"></div>
  <div class="brand-foot">NURQALAM ACADEMY</div>

  <nav class="footer-nav"><span>HOME</span><span>ABOUT US</span><span>OUR COURSES</span><span>CONTACT US</span></nav>

  <div class="footer-label" style="left:894px;top:58px">FOLLOW US</div>
  <div class="icon-dot" style="left:892px;top:108px;width:30px;height:30px"></div>
  <div class="social-text" style="left:935px;top:104px">Like us on<br>CIRCLEPAGE</div>
  <div class="icon-dot" style="left:892px;top:171px;width:30px;height:30px"></div>
  <div class="social-text" style="left:935px;top:169px">Follow us on<br>CHIRPLINE</div>
  <div class="icon-dot" style="left:892px;top:233px;width:30px;height:30px"></div>
  <div class="social-text" style="left:935px;top:229px">Follow us on<br>WORKLINK</div>

  <div class="footer-rule"></div>
  <div class="copyright">Copyright © 2020 All Rights Reserved</div>
</footer>

</body>
</html>
```